Fancy flyer to entice High School Students

http://kestrelvane.com needs a marketing slick/flyer to pass out. The marketing text is below(feel free to place where you think appropriate).

* 8th grade to 12th grade (or 8th graders to 12th graders)
* Land a real job internship(instead of Pelkroft)
* 100's of internships available
* Learn how to start your own business out of High School making way more than minimum wage
* In college when interviewing for an internship don't be the guy that answers "no, sorry, this would be my first internship" putting you at a huge disadvantage"
* Fill in the Contact Us form at http://kestrelvane.com at the bottom left corner to find out more information

We will be evaluating design with this blog post in mind....
http://trundlepostnotes.com/color-influence-buyers/

We like attention grabbing contact us type stuff and calls to action. If you feel it is appropriate to change the marketing text to make your flyer stand out, please feel free. I am not the best at marketing and am the first to admit it.
Updates

A simple 8.5 x 11 flyer would be great.

Target Market(s)

High School students, male and female with high grade point averages(smart students). For the top 20% of their class.

Industry/Entity Type

Marketing

Requirements
Must have
• good call to action

```html
<!DOCTYPE html>
<html lang="en">
<head>
<meta charset="utf-8">
<title>Kestrel Vane Software – Internship Flyer</title>
<link rel="stylesheet" href="https://fonts.googleapis.com/css2?family=Open+Sans:wght@400;600&family=Roboto+Condensed:wght@400;700&display=swap">
<style>
  :root {
    --amber-top: #d9952a;
    --amber-light: #f3d9a2;
    --cream: #fdf5e6;
    --cream-deep: #efc27a;
    --ink: #3a3a3a;
    --navy: #2b3590;
    --crimson: #d81b60;
    --bronze: #c27a22;
    --green: #3cb54a;
    --rose: #e0479a;
    --violet: #6b3fa0;
    --band-dark: #2f2f2f;
    --footer: #353535;
    --footer-line: #8a8a8a;
    --label: #f0a030;
    --white: #ffffff;
  }
  * { margin: 0; padding: 0; box-sizing: border-box; }
  html, body { width: 931px; height: 1200px; overflow: hidden; background: #ffffff; }
  .flyer {
    position: relative; width: 931px; height: 1200px; overflow: hidden;
    background: var(--cream);
    font-family: "Open Sans", sans-serif;
  }
  .hero {
    position: absolute; left: 0; top: 0; width: 931px; height: 700px;
    background: radial-gradient(ellipse at 75% 15%, #fbe7bd 0%, var(--amber-light) 30%, var(--amber-top) 85%);
  }
  .photo { position: absolute; }
  .photo-group {
    left: 258px; top: 22px; width: 673px; height: 560px; border-radius: 160px 160px 0 0;
    background: linear-gradient(180deg, #d9b48a 0%, #efe6de 50%, #e3dccd 100%);
  }
  .photo-left {
    left: 29px; top: 112px; width: 255px; height: 440px; border-radius: 110px 110px 0 0;
    background: linear-gradient(180deg, #b98a5e 0%, #6f93b8 55%, #4f7aa3 100%);
  }
  .brand {
    position: absolute; left: 41px; top: 50px; display: flex; align-items: center; gap: 10px;
    font-family: "Open Sans", sans-serif; font-weight: 600; font-size: 34px; color: var(--ink);
    letter-spacing: -0.5px;
  }
  .brand-dot { width: 24px; height: 24px; border-radius: 50%; background: var(--ink); }
  .waves { position: absolute; left: 0; top: 0; width: 931px; height: 1200px; }
  .lower-glow {
    position: absolute; left: 0; top: 0; width: 931px; height: 1200px;
  }
  .photo-student {
    left: 12px; top: 645px; width: 263px; height: 474px; border-radius: 110px 110px 0 0;
    background: linear-gradient(180deg, #b98a5e 0%, #f0c9d4 40%, #e8a7bd 70%, #7d9fc4 100%);
  }
  .headline {
    position: absolute; left: 304px; top: 560px;
    font-family: "Roboto Condensed", sans-serif; font-weight: 700; font-size: 50px; line-height: 54px;
    color: var(--ink); letter-spacing: 0.2px;
  }
  .contact {
    position: absolute; left: 304px; top: 700px; display: flex; align-items: baseline; gap: 12px;
    font-family: "Roboto Condensed", sans-serif; font-weight: 700;
  }
  .contact-label { font-size: 32px; color: var(--navy); }
  .contact-phone { font-size: 38px; color: var(--ink); }
  .points { position: absolute; left: 291px; top: 790px; width: 640px; list-style: none; }
  .point {
    color: var(--white); font-size: 17px; line-height: 22px; text-align: justify;
    padding: 7px 50px 7px 16px; margin-bottom: 8px; border-radius: 8px 0 0 8px;
  }
  .point-crimson { background: var(--crimson); }
  .point-bronze { background: var(--bronze); }
  .point-green { background: var(--green); }
  .point-rose { background: var(--rose); }
  .point-violet { background: var(--violet); padding-top: 8px; padding-bottom: 8px; }
  .footer {
    position: absolute; left: 0; top: 1119px; width: 931px; height: 81px; background: var(--footer);
    border-top: 4px solid var(--footer-line);
    display: flex; padding: 12px 0 0 54px; color: var(--white); font-size: 18px; line-height: 25px;
  }
  .footer-item { width: 254px; }
  .footer-item.web { width: 282px; }
  .footer-item.address { width: auto; }
  .footer-label { color: var(--label); font-weight: 600; }
</style>
</head>
<body>
<main class="flyer">
  <section class="hero">
    <div class="photo photo-group" role="img" aria-label="Photo of three smiling high school girls holding notebooks and folders"></div>
    <div class="photo photo-left" role="img" aria-label="Photo of a smiling student in a denim jacket holding books"></div>
    <div class="brand"><span>Kestrel Vane Software</span><span class="brand-dot"></span></div>
  </section>

  <svg class="waves" viewBox="0 0 931 1200" aria-hidden="true">
    <defs>
      <linearGradient id="cream-fade" x1="0" y1="0" x2="0" y2="1">
        <stop offset="0" stop-color="#fdf5e6"/>
        <stop offset="0.45" stop-color="#fbecd0"/>
        <stop offset="1" stop-color="#efc27a"/>
      </linearGradient>
    </defs>
    <path d="M0 680 C280 540 600 520 931 585 L931 1200 L0 1200 Z" fill="url(#cream-fade)"/>
    <path d="M0 490 C250 460 500 455 931 545 L931 575 C600 500 300 500 0 590 Z" fill="var(--crimson)"/>
    <path d="M0 575 C250 495 600 475 931 560 L931 590 C600 525 280 545 0 690 Z" fill="var(--band-dark)"/>
    <path d="M380 475 C600 458 800 500 931 552" stroke="var(--green)" stroke-width="10" fill="none"/>
  </svg>

  <div class="photo photo-student" role="img" aria-label="Photo of a student with a backpack in a pink striped top holding a laptop"></div>

  <h1 class="headline">WE PROVIDE<br>REAL INTERSHIP !</h1>

  <div class="contact">
    <span class="contact-label">Contact us today</span>
    <span class="contact-phone">(720) 555-0148</span>
  </div>

  <ul class="points">
    <li class="point point-crimson">8th graders to 12th graders)</li>
    <li class="point point-bronze">Land a real job internship (instead of Pelkroft)</li>
    <li class="point point-green">100's of internships available</li>
    <li class="point point-rose">Learn how to start your own business out of High School making way more than minimum wage</li>
    <li class="point point-violet">In college when interviewing for an internship don't be the guy that answers "no, sorry, this would be my first internship" putting you at a huge disadvantage"</li>
  </ul>

  <footer class="footer">
    <div class="footer-item"><div class="footer-label">Email</div><div>info@kestrelvane.com</div></div>
    <div class="footer-item web"><div class="footer-label">Web</div><div>www.kestrelvane.com</div></div>
    <div class="footer-item address"><div><span class="footer-label">Add</span> : 4180 Larkspur Ave.</div><div>#214, Fairhollow, CO 80517</div></div>
  </footer>
</main>
</body>
</html>
```